Print and E-book Personal Injury Front and Back Book Cover

I need a book cover for a personal injury law firm book titled "Steady Ground Ahead" with the subtitle "A Practical Guide for Accident Claims." The book cover should have an image. This isas a lead generation book designed to be give to potential clients to have them sign as new clients.

Target Market(s)

Potential New Clients Looking For a Personal Injury Attorney

Industry/Entity Type

Legal

Requirements
Must have
• Title and some type of image or images

```html
<!DOCTYPE html>
<html lang="en">
<head>
<meta charset="utf-8">
<title>Steady Ground Ahead – Book Cover</title>
<link href="https://fonts.googleapis.com/css2?family=Cinzel:wght@400;700;900&family=Source+Sans+3:wght@400&display=swap" rel="stylesheet">
<style>
  :root {
    --stage: #2b2b2b;
    --gold-dark: #a8821a;
    --gold-mid: #c89d2a;
    --gold-light: #e0b93e;
    --paper: #ffffff;
    --paper-shade: #ececec;
    --ink-white: #ffffff;
    --photo-deep: #14110d;
    --photo-warm: #4a3420;
    --photo-navy: #1d2536;
  }
  * { margin: 0; padding: 0; box-sizing: border-box; }
  html, body { width: 1200px; height: 386px; overflow: hidden; background: var(--stage); }
  .wraparound {
    position: absolute; left: 318px; top: 0;
    width: 564px; height: 386px; display: flex;
  }
  /* back cover + spine */
  .back {
    position: relative; width: 306px; height: 386px;
    background: linear-gradient(90deg, var(--gold-dark) 0%, var(--gold-light) 45%, var(--gold-mid) 80%, var(--gold-dark) 100%);
    color: var(--ink-white);
  }
  .back-title {
    position: absolute; left: 0; width: 258px; top: 22px;
    text-align: center; font-family: "Cinzel", serif; font-weight: 400; line-height: 0.9;
  }
  .back-title .big { display: block; font-size: 33px; }
  .back-title .small { display: block; font-size: 21px; font-weight: 700; margin-top: 3px; }
  .back-subtitle {
    position: absolute; left: 0; width: 258px; top: 105px; text-align: center;
    font-family: "Cinzel", serif; font-size: 8.2px; font-weight: 700; letter-spacing: 0.2px;
  }
  .blurb {
    position: absolute; left: 20px; width: 214px; top: 123px;
    font-family: "Source Sans 3", sans-serif; font-size: 6.9px; line-height: 10.2px;
    text-align: justify; text-align-last: center;
  }
  .blurb p + p { margin-top: 10.8px; }
  .spine-title, .spine-author {
    position: absolute; writing-mode: vertical-rl; font-family: "Cinzel", serif;
    color: var(--ink-white); white-space: nowrap;
  }
  .spine-title { left: 273px; top: 22px; font-size: 17px; }
  .spine-author { left: 276px; top: 280px; font-size: 10.5px; }
  /* front cover */
  .front { position: relative; width: 258px; height: 386px; background: var(--paper); }
  .front-head {
    position: absolute; left: 0; top: 0; width: 258px; height: 165px;
    background: linear-gradient(180deg, var(--paper) 60%, var(--paper-shade) 100%);
    text-align: center;
  }
  .gold-text {
    background: linear-gradient(180deg, #f3d36a 0%, #b8891b 45%, #e8c24c 60%, #8a6512 100%);
    -webkit-background-clip: text; background-clip: text; color: transparent;
    font-family: "Cinzel", serif;
  }
  .front-subtitle {
    position: absolute; left: 0; width: 100%; top: 24px; font-size: 8.3px; font-weight: 700;
  }
  .front-title { position: absolute; left: 0; width: 100%; top: 38px; line-height: 0.98; }
  .front-title .big { display: block; font-size: 44px; font-weight: 700; }
  .front-title .small { display: block; font-size: 27px; font-weight: 700; margin-top: -2px; }
  .cover-photo {
    position: absolute; left: 0; top: 165px; width: 258px; height: 173px;
    background:
      radial-gradient(ellipse at 75% 35%, var(--photo-navy) 0%, transparent 55%),
      radial-gradient(ellipse at 55% 80%, #d8d8d8 0%, transparent 30%),
      linear-gradient(180deg, var(--photo-deep) 0%, var(--photo-warm) 55%, var(--photo-deep) 100%);
  }
  .front-author {
    position: absolute; left: 0; width: 100%; top: 350px; text-align: center;
    font-size: 15px; font-weight: 700;
  }
</style>
</head>
<body>
  <div class="wraparound">
    <section class="back">
      <h2 class="back-title"><span class="big">Steady<br>Ground</span><span class="small">Ahead</span></h2>
      <p class="back-subtitle">A Practical Guide for Accident Claims</p>
      <div class="blurb">
        <p>Lorem ipsum dolor sit amet, consectetur adipiscing elit, sed do eiusmod tempor incididunt ut labore et dolore magna aliqua. Quis ipsum suspendisse ultrices gravida. Risus commodo viverra maecenas accumsan lacus vel facilisis. Lorem ipsum dolor sit amet, consectetur adipiscing elit, sed do eiusmod tempor incididunt ut labore et dolore magna aliqua. Quis ipsum suspendisse ultrices gravida. Risus commodo viverra maecenas accumsan lacus vel facilisis.</p>
        <p>Lorem ipsum dolor sit amet, consectetur adipiscing elit, sed do eiusmod tempor incididunt ut labore et dolore magna aliqua. Quis ipsum suspendisse ultrices gravida. Risus commodo viverra maecenas accumsan lacus vel facilisis. Lorem ipsum dolor sit amet, consectetur adipiscing elit, sed do eiusmod tempor incididunt ut labore et dolore magna aliqua. Quis ipsum suspendisse ultrices gravida. Risus commodo viverra maecenas accumsan lacus vel facilisis.</p>
        <p>Lorem ipsum dolor sit amet, consectetur adipiscing elit, sed do eiusmod tempor incididunt ut labore et dolore magna aliqua. Quis ipsum suspendisse ultrices gravida. Risus commodo viverra maecenas accumsan lacus vel facilisis. Lorem ipsum dolor sit amet, consectetur adipiscing elit, sed do eiusmod tempor incididunt ut labore et dolore magna aliqua. Quis ipsum suspendisse ultrices gravida. Risus commodo viverra maecenas accumsan lacus vel facilisis.</p>
      </div>
      <span class="spine-title">Steady Ground Ahead</span>
      <span class="spine-author">Author Name</span>
    </section>
    <section class="front">
      <div class="front-head">
        <p class="front-subtitle gold-text">A Practical Guide for Accident Claims</p>
        <h1 class="front-title gold-text"><span class="big">Steady</span><span class="big">Ground</span><span class="small">Ahead</span></h1>
      </div>
      <div class="cover-photo" role="img" aria-label="Photo of a lawyer in a dark suit signing documents at a desk beside scales of justice and a gavel"></div>
      <p class="front-author gold-text">Author Name</p>
    </section>
  </div>
</body>
</html>
```